Fitness Equipment & Service

I want to make the card eye catching and fun. We are called Corvane Motion Limited and we are based in Wales. We sell, install and service all types of fitness equipment from Skipping ropes, right through the Dumbbells, Kettle bells and Barbells through to state of the art Treadmills, Running Machines and Strength Equipment. We also design and install changing room furniture and lockers.

TYPOGRAPHY
We would like to use Futrura. Futura has an appearance of efficiency and forwardness. The typeface is derived
from simple geometric forms (near-perfect circles, triangles and squares) and is based on strokes of
near-even weight, which are low in contrast. This is most visible in the almost perfectly round stroke of
the o, which is nonetheless slightly ovoid.
The lowercase has tall ascenders, which rise above the cap line. The uppercase
characters present proportions similar to those of classical Roman capitals.

TYPOGRAPHIC CONSIDERATIONS
No Strike though
No Horizontal Scaling
No Drop Shadows
No Effects
Never use less than 120% Leading

OUR CORPORATE COLOURS
BRAND GUIDELINES
We were thinking that our primary colour palette consists of the Acid Green (Pantone 382) and Process Black.

We work closely with tquarly Ltd and would like to include their name on the card somewhere. I have attached images of the other brands that we work with as an idea or the small icons I have included that illustrate what we do?. I have very kindly been given permission to use any of the images off the files that I have included below, so I hope these help. I will include these below. I would be open to suggestions if it made the card more striking Can you do it?
Updates

Hi All, Just wanted to add a few thoughts but you are the guys with the creative visions (thats why are here) We are based in Wales, UK and we would be open to lots of different ideas on a theme but must be eye catching, Bold and FUN. If you can or think that the Welsh or any dragon could be put in there then go for it (its not a must have) We have also added some ideas for colour but again its over to you!! GO FOR IT ! Thanks and look forward to your visions! Owen

Hi All, Just thought I would sen through the contact details that need to be on the card. (if you want to play around with icons instead of the wording twitter, Facebook, go for it): Corvane Motion Limited Owen Pritchard Managing Director Mob: +44 (0)7582 913 406 e-mail: sales@corvanemotion.co.uk Web: Corvanemotion.co.uk twitter: @motionLetterbin Facebook: Corvane Motion Limited

```html
<!DOCTYPE html>
<html lang="en">
<head>
<meta charset="utf-8">
<title>Corvane Motion Limited – Business Card</title>
<link href="https://fonts.googleapis.com/css2?family=Open+Sans:wght@400;600;700&display=swap" rel="stylesheet">
<style>
  :root {
    --backdrop-light: #d2d2d2;
    --backdrop-dark: #bdbdbd;
    --card-white: #ffffff;
    --brand-blue: #1e69b0;
    --brand-navy: #1b3a84;
    --ink-grey: #454545;
    --deep-navy: #0c1a3a;
    --mid-blue: #1d4f8f;
    --band-black: rgba(12, 12, 14, 0.9);
  }
  * { margin: 0; padding: 0; box-sizing: border-box; }
  html, body {
    width: 1200px; height: 900px; overflow: hidden;
  }
  body {
    position: relative;
    background: radial-gradient(ellipse at 50% 40%, var(--backdrop-light), var(--backdrop-dark));
    font-family: "Open Sans", Arial, sans-serif;
  }
  .card {
    position: absolute; top: 170px; width: 347px; height: 561px; overflow: hidden;
  }
  /* Front */
  .card-front { left: 259px; background: var(--card-white); }
  .accent-bar {
    position: absolute; left: 102px; width: 143px; background: var(--brand-blue);
  }
  .accent-bar--top { top: 0; height: 30px; }
  .accent-bar--bottom { bottom: 0; height: 28px; }
  .brand-mark {
    position: absolute; top: 78px; left: 0; width: 100%;
    display: flex; flex-direction: column; align-items: center; gap: 16px;
  }
  .brand-dot {
    width: 120px; height: 120px; border-radius: 50%; background: var(--brand-navy);
  }
  .brand-name {
    font-weight: 700; font-size: 20px; line-height: 1.2; color: var(--brand-navy);
    text-align: center;
  }
  .person {
    position: absolute; top: 316px; width: 100%; text-align: center;
  }
  .person-name { font-weight: 700; font-size: 18px; line-height: 1.25; color: var(--brand-navy); }
  .person-role { font-size: 14.5px; line-height: 1.3; color: var(--ink-grey); }
  .contact-list {
    position: absolute; top: 384px; width: 100%; list-style: none;
    display: flex; flex-direction: column; align-items: center;
  }
  .contact-item {
    display: flex; align-items: center; gap: 6px;
    font-size: 15px; line-height: 20px; color: var(--ink-grey);
  }
  .contact-icon { width: 11px; height: 11px; flex: none; fill: var(--brand-navy); }
  /* Back */
  .card-back {
    left: 631px;
    background: linear-gradient(160deg, var(--mid-blue) 0%, #163d74 45%, var(--deep-navy) 100%);
  }
  .tile-grid { position: absolute; inset: 0; }
  .tile-grid rect { fill: #ffffff; }
  .name-band {
    position: absolute; left: 0; top: 426px; width: 100%; height: 74px;
    background: var(--band-black);
    display: flex; align-items: center; padding-left: 40px;
  }
  .band-name {
    font-weight: 400; font-size: 19px; line-height: 1.2; letter-spacing: 2px;
    color: #ffffff; text-transform: uppercase;
  }
</style>
</head>
<body>

<section class="card card-front" aria-label="Card front">
  <div class="accent-bar accent-bar--top"></div>

  <div class="brand-mark">
    <div class="brand-dot"></div>
    <p class="brand-name">Corvane Motion Limited</p>
  </div>

  <div class="person">
    <p class="person-name">Owen Pritchard</p>
    <p class="person-role">Managing Director</p>
  </div>

  <ul class="contact-list">
    <li class="contact-item">
      <svg class="contact-icon" viewBox="0 0 12 12"><path d="M2.5 0.5l2 2.2-1 1.3c.7 1.6 2 2.9 3.5 3.5l1.3-1 2.2 2-1.2 2C5 10.3 1.7 7 .5 1.7z"/></svg>
      +44 (0)7582 913 406
    </li>
    <li class="contact-item">
      <svg class="contact-icon" viewBox="0 0 12 12"><path d="M0 2.5h12v7H0z"/><path d="M0 2.5l6 4 6-4" fill="none" stroke="#fff" stroke-width="1"/></svg>
      sales@corvanemotion.co.uk
    </li>
    <li class="contact-item">
      <svg class="contact-icon" viewBox="0 0 12 12"><circle cx="6" cy="6" r="6"/><path d="M0 6h12M6 0c-3 3-3 9 0 12M6 0c3 3 3 9 0 12" fill="none" stroke="#fff" stroke-width=".8"/></svg>
      Corvanemotion.co.uk
    </li>
    <li class="contact-item">
      <svg class="contact-icon" viewBox="0 0 12 12"><rect width="12" height="12" rx="2"/></svg>
      @motionLetterbin
    </li>
    <li class="contact-item">
      <svg class="contact-icon" viewBox="0 0 12 12"><rect width="12" height="12" rx="2"/></svg>
      Corvane Motion Limited
    </li>
  </ul>

  <div class="accent-bar accent-bar--bottom"></div>
</section>

<section class="card card-back" role="img" aria-label="Collage of gym photographs with white equipment and service icons in a blue tiled grid">
  <svg class="tile-grid" viewBox="0 0 347 561" width="347" height="561" aria-hidden="true">
    <rect x="0" y="0" width="78" height="92" opacity=".12"/>
    <rect x="172" y="0" width="94" height="92" opacity=".18"/>
    <rect x="266" y="0" width="81" height="92" opacity=".28"/>
    <rect x="0" y="92" width="78" height="95" opacity=".06"/>
    <rect x="78" y="92" width="94" height="95" opacity=".25"/>
    <rect x="172" y="92" width="94" height="95" opacity=".3"/>
    <rect x="266" y="92" width="81" height="95" opacity=".1"/>
    <rect x="0" y="187" width="78" height="94" opacity=".08"/>
    <rect x="172" y="187" width="94" height="94" opacity=".06"/>
    <rect x="266" y="187" width="81" height="94" opacity=".2"/>
    <rect x="0" y="281" width="78" height="95" opacity=".22"/>
    <rect x="78" y="281" width="94" height="95" opacity=".3"/>
    <rect x="172" y="281" width="94" height="95" opacity=".14"/>
    <rect x="78" y="376" width="94" height="50" opacity=".22"/>
    <rect x="172" y="376" width="94" height="50" opacity=".1"/>
    <rect x="78" y="500" width="94" height="61" opacity=".18"/>
    <rect x="266" y="500" width="81" height="61" opacity=".14"/>
  </svg>
  <div class="name-band">
    <p class="band-name">Corvane Motion Limited</p>
  </div>
</section>

</body>
</html>
```